New, modern business card for growing audiology practice

We need a new business card for our audiology practice. Our logo and website have recently changed (more modern) and we want our business cards to reflect this change.
We conduct hearing tests, perform earwax removals, and fit & dispense hearing aids to our patients. We are a family owned practice in which the owner is the one who works directly with the patient. I have attached logos in various formats to use, as well as two ideas I found on this website; as well as a scanned copy of our current logo. Good luck!

Industry/Entity Type

Business

Contact Information for Business Card

Company name: Tolvera Hearing Center
Provider name: Peter Wolstenby, Au.D. F/NSB
Phone number: (440) 683-5127
Address: 837 W. Lindell Ave. Marlow Falls, OH 44817
email: tolverahearing@postvane.com
website: tolverahearing.com

Colors
000000
aaaaaa
dbdbdb
cacaca
9bcb3c
afd23c
cadf82
b1b1b1

Requirements
Must have
• My card must include information in the "details" section. In the attached images, I found a few that I liked and I would like to model after - "brisky bouncin'" and "Sound Method Center".
• Must be horizontal.
• Must include logos provided. I uploaded them in various file formats and various ways.
• Must match logo font, if possible, if not, please get as close as you can.
Nice to have
• I really like the idea of having a color on one side with just the logo and company name and the contact information and provider name on the other side. I also really like the idea of having the main color dominating on the logo/company side with accent of that same color on the contact side of the card.
Should not have
• Must not be vertical.

```html
<!DOCTYPE html>
<html lang="en">
<head>
<meta charset="utf-8">
<title>Tolvera Hearing Center – Business Card</title>
<link rel="stylesheet" href="https://fonts.googleapis.com/css2?family=Open+Sans:wght@300;400;600;700&display=swap">
<style>
  :root {
    --backdrop: #2f2b28;
    --card: #0b0b0b;
    --green: #7fb23c;
    --green-light: #9bcb3c;
    --white: #ffffff;
    --text-soft: #e6e6e6;
    --silver: #cacaca;
    --rule: #2a2a2a;
  }
  * { margin: 0; padding: 0; box-sizing: border-box; }
  html, body {
    width: 1200px; height: 900px; overflow: hidden;
    background: var(--backdrop);
    font-family: "Open Sans", Arial, sans-serif;
  }
  .stage {
    width: 1200px; height: 900px;
    display: flex; align-items: center; justify-content: center; gap: 60px;
  }
  .card {
    width: 525px; height: 300px;
    background: var(--card);
    position: relative;
    box-shadow: 0 10px 30px rgba(0,0,0,.45);
  }
  /* contact side */
  .brand-block {
    position: absolute; left: 34px; top: 0; bottom: 0; width: 190px;
    display: flex; flex-direction: column; justify-content: center; gap: 12px;
  }
  .brand-dot {
    width: 46px; height: 46px; border-radius: 50%;
    background: var(--green);
  }
  .brand-name {
    color: var(--green); font-weight: 600; font-size: 24px; line-height: 1.15;
  }
  .divider {
    position: absolute; left: 236px; top: 70px; bottom: 40px;
    width: 1px; background: var(--rule);
  }
  .details {
    position: absolute; left: 262px; top: 58px; right: 16px;
    color: var(--white);
  }
  .provider { font-size: 17px; font-weight: 700; white-space: nowrap; }
  .provider .surname { color: var(--green-light); }
  .provider .credentials { font-size: 11px; }
  .address { margin-top: 10px; font-size: 12px; font-weight: 400; line-height: 1.45; color: var(--text-soft); }
  .contact-list { list-style: none; margin-top: 14px; font-size: 13px; line-height: 1.55; }
  .contact-list li { display: flex; align-items: center; gap: 9px; white-space: nowrap; }
  .contact-list svg { width: 11px; height: 11px; flex: none; }
  /* logo side */
  .card--logo { display: flex; align-items: center; justify-content: center; }
  .logo-lockup { display: flex; align-items: center; gap: 12px; }
  .logo-mark { width: 14px; height: 14px; border-radius: 50%; background: var(--silver); }
  .logo-name {
    color: var(--silver); font-weight: 300; font-size: 21px;
    letter-spacing: 1px; text-transform: uppercase; white-space: nowrap;
  }
</style>
</head>
<body>
<main class="stage">
  <section class="card card--contact">
    <div class="brand-block">
      <span class="brand-dot"></span>
      <span class="brand-name">Tolvera Hearing Center</span>
    </div>
    <span class="divider"></span>
    <div class="details">
      <p class="provider">Peter <span class="surname">Wolstenby</span><span class="credentials">, Au.D. F/NSB</span></p>
      <p class="address">837 W. Lindell<br>Ave. Marlow Falls, OH 44817</p>
      <ul class="contact-list">
        <li>
          <svg viewBox="0 0 12 12" aria-hidden="true"><path fill="#7fb23c" d="M2.5 1l2 2.3-1 1.2c.7 1.6 2 2.9 3.5 3.6l1.2-1 2.3 2-1.2 1.6C5.5 10.5 1.5 6.5 1.2 2.2z"/></svg>
          (440) 683-5127
        </li>
        <li>
          <svg viewBox="0 0 12 12" aria-hidden="true"><rect x="1" y="2.5" width="10" height="7" fill="#7fb23c"/><path d="M1 2.5l5 4 5-4" fill="none" stroke="#0b0b0b" stroke-width="1"/></svg>
          tolverahearing@postvane.com
        </li>
        <li>
          <svg viewBox="0 0 12 12" aria-hidden="true"><circle cx="6" cy="6" r="5" fill="#7fb23c"/><path d="M1 6h10M6 1c-2 2.5-2 7.5 0 10M6 1c2 2.5 2 7.5 0 10" fill="none" stroke="#0b0b0b" stroke-width=".8"/></svg>
          tolverahearing.com
        </li>
      </ul>
    </div>
  </section>

  <section class="card card--logo">
    <div class="logo-lockup">
      <span class="logo-mark"></span>
      <span class="logo-name">Tolvera Hearing Center</span>
    </div>
  </section>
</main>
</body>
</html>
```